Business Card Design Project

I am opening a skin care studio called Glow Haven by Marisol. I will be offering a wide range of unique and affordable skin services including facials, chemical peels, microdermabrasion treatments, body wraps, salt glows, all waxing and eye lash extensions. If the business cards depicts what I would like, this would lead to brochures, web design, signs, etc.

Project Deadline Extended
Reason: A request to extend deadline was requested. I will be more than happy to accommodate.

Industry/Entity Type

Business

Requirements
Nice to have
• facial features so prospective client clearly identifies what type of business this is. Not stuffy or boring "spa" looking graphics. I am focusing just on face, body, waxing, eyelashes. No massage or nails.

```html
<!DOCTYPE html>
<html lang="en">
<head>
<meta charset="utf-8">
<title>Glow Haven by Marisol – Appointment Card</title>
<link rel="stylesheet" href="https://fonts.googleapis.com/css2?family=Dancing+Script:wght@700&family=Open+Sans:ital,wght@1,700&display=swap">
<style>
  :root {
    --ink: #000000;
    --paper: #ffffff;
    --brand-pink: #ff3fd6;
    --text-dark: #1a1a1a;
    --rule: #333333;
    --skin-light: #c9b3a6;
    --skin-mid: #8d7467;
  }
  html, body {
    margin: 0;
    padding: 0;
    width: 1200px;
    height: 675px;
    overflow: hidden;
    background: var(--paper);
  }
  .card {
    position: relative;
    width: 1200px;
    height: 675px;
    overflow: hidden;
    background: linear-gradient(to bottom, var(--ink) 0, var(--ink) 340px, #3a3a3a 400px, #bdbdbd 450px, var(--paper) 490px, var(--paper) 100%);
    font-family: "Open Sans", Arial, sans-serif;
  }
  .hero-photo {
    position: absolute;
    left: 540px;
    top: 0;
    width: 660px;
    height: 440px;
    background: radial-gradient(ellipse 60% 55% at 50% 45%, var(--skin-light) 0%, var(--skin-mid) 45%, rgba(0,0,0,0) 85%);
    -webkit-mask-image: linear-gradient(to bottom, #000 70%, transparent 100%);
    mask-image: linear-gradient(to bottom, #000 70%, transparent 100%);
  }
  .brand-name {
    position: absolute;
    left: 26px;
    top: 30px;
    margin: 0;
    font-family: "Dancing Script", cursive;
    font-weight: 700;
    font-size: 104px;
    line-height: 112px;
    color: var(--brand-pink);
    white-space: nowrap;
  }
  .brand-name .line-two {
    display: block;
    padding-left: 112px;
  }
  .website {
    position: absolute;
    left: 40px;
    top: 300px;
    margin: 0;
    font-style: italic;
    font-weight: 700;
    font-size: 32px;
    line-height: 44px;
    color: var(--paper);
    white-space: nowrap;
  }
  .appointment-field {
    position: absolute;
    left: 58px;
    width: 1086px;
    display: flex;
    align-items: flex-end;
    font-style: italic;
    font-weight: 700;
    font-size: 27px;
    line-height: 36px;
    color: var(--text-dark);
  }
  .appointment-field .label { width: 264px; white-space: nowrap; }
  .appointment-field .fill-line {
    flex: 1;
    border-bottom: 2px solid var(--rule);
    margin-bottom: 8px;
  }
  .field-date { top: 510px; }
  .field-time { top: 578px; }
  .contact-line {
    position: absolute;
    left: 322px;
    top: 632px;
    margin: 0;
    font-style: italic;
    font-weight: 700;
    font-size: 21px;
    line-height: 28px;
    color: var(--text-dark);
    white-space: nowrap;
  }
</style>
</head>
<body>
  <main class="card">
    <div class="hero-photo" role="img" aria-label="Space for a close-up beauty portrait photograph"></div>

    <h1 class="brand-name">Glow Haven<span class="line-two">by Marisol</span></h1>

    <p class="website">www.glowhavenbymarisol.com</p>

    <div class="appointment-field field-date">
      <span class="label">Appointment Date:</span>
      <span class="fill-line"></span>
    </div>
    <div class="appointment-field field-time">
      <span class="label">Appointment Time:</span>
      <span class="fill-line"></span>
    </div>

    <p class="contact-line">1842 Alder Avenue Fairbrook, CO 80999 • 555-014-2290</p>
  </main>
</body>
</html>
```